Local Flower Farm Needs Business Card Design

I need business cards designed for a flower farm based in Eudora, Kansas.
Business Info:
We are a local cut flower farm located in Eudora, Kansas, founded by Corinne Haldwick. What started as a passion for agriculture and search for more joy in daily life has blossomed into a small business dedicated to providing the community with beautiful, fresh, and sustainable flowers. We specialize in local, seasonal blooms, ensuring that every petal reflects the care and dedication we pour into our craft. Our mission is to deliver the highest quality flowers directly to our customers through local farmers markets and to florists who share our commitment to sustainability. Join us in celebrating the beauty of nature, one bloom at a time!
Contact Details:
Corinne Haldwick
Owner
Phone 913-555-0147
Facebook: Rosalind Thorpe Gardens
Instagram: @RosalindThorpeGardens
Website: RosalindThorpeGardens.example
Target Market(s)
Wholesale to Florists and Direct to Consumer via Farmers Market
Industry/Entity Type
Florist, Farm
Contact Information for Business Card
Name, Contact Info, Logo
Look and feel
Each slider illustrates characteristics of the customer's brand and the style your logo design should communicate.

```html
<!DOCTYPE html>
<html lang="en">
<head>
<meta charset="utf-8">
<title>Rosalind Thorpe Gardens – Business Card</title>
<link href="https://fonts.googleapis.com/css2?family=Montserrat:wght@400;500;700&display=swap" rel="stylesheet">
<style>
  :root {
    --ink: #0a272c;
    --ink-soft: #2f5257;
    --paper: #ffffff;
    --backdrop: #9c9c9c;
    --line: #7d8a8c;
  }
  * { box-sizing: border-box; margin: 0; padding: 0; }
  html, body { width: 1093px; height: 1200px; overflow: hidden; }
  body {
    background: var(--backdrop);
    font-family: "Montserrat", Arial, sans-serif;
    position: relative;
  }
  .card {
    position: absolute;
    left: 264px;
    width: 597px;
    height: 364px;
    border-radius: 16px;
    overflow: hidden;
  }
  .card--front { top: 224px; background: var(--paper); }
  .card--back { top: 615px; height: 368px; background: var(--ink); }

  .monogram-art {
    position: absolute;
    left: 0; top: 0;
    width: 246px; height: 100%;
    background: linear-gradient(160deg, var(--ink) 0%, var(--ink-soft) 100%);
  }
  .brand-badge {
    position: absolute;
    display: flex; align-items: center; justify-content: center;
    border-radius: 50%;
    text-align: center;
    font-weight: 500;
    letter-spacing: 0.06em;
    text-transform: uppercase;
  }
  .card--front .brand-badge {
    left: 286px; top: 17px;
    width: 163px; height: 163px;
    border: 1.5px solid var(--line);
    color: var(--ink);
    font-size: 15px; line-height: 1.35;
  }
  .card--back .brand-badge {
    left: 174px; top: 70px;
    width: 250px; height: 250px;
    border: 1px solid var(--paper);
    color: var(--paper);
    font-size: 21px; line-height: 1.4;
  }
  .holder {
    position: absolute; left: 288px; top: 198px;
    color: var(--ink);
  }
  .holder__name { font-size: 22px; font-weight: 700; line-height: 1.1; }
  .holder__role { font-size: 12.5px; font-weight: 400; margin-top: 4px; }
  .contacts {
    position: absolute; left: 288px; top: 258px;
    list-style: none; color: var(--ink);
    font-size: 13.5px; font-weight: 400;
  }
  .contacts li {
    display: flex; align-items: center;
    height: 21.5px;
  }
  .contacts svg { width: 13px; height: 13px; margin-right: 7px; flex: none; }
</style>
</head>
<body>
  <section class="card card--front">
    <div class="monogram-art" role="img" aria-label="Large brand monogram with line-drawn wildflower stems"></div>
    <div class="brand-badge">Rosalind<br>Thorpe<br>Gardens</div>
    <div class="holder">
      <p class="holder__name">Corinne Haldwick</p>
      <p class="holder__role">Owner</p>
    </div>
    <ul class="contacts">
      <li>
        <svg viewBox="0 0 24 24" aria-hidden="true"><path fill="#0a272c" d="M6.6 10.8a15 15 0 0 0 6.6 6.6l2.2-2.2c.3-.3.7-.4 1-.2 1.1.4 2.3.6 3.6.6.6 0 1 .4 1 1V20c0 .6-.4 1-1 1A17 17 0 0 1 3 4c0-.6.4-1 1-1h3.5c.6 0 1 .4 1 1 0 1.3.2 2.5.6 3.6.1.3 0 .7-.2 1z"/></svg>
        913-555-0147
      </li>
      <li>
        <svg viewBox="0 0 24 24" aria-hidden="true"><circle cx="12" cy="12" r="10" fill="none" stroke="#0a272c" stroke-width="2.4"/></svg>
        Rosalind Thorpe Gardens
      </li>
      <li>
        <svg viewBox="0 0 24 24" aria-hidden="true"><rect x="2.5" y="2.5" width="19" height="19" rx="5" fill="none" stroke="#0a272c" stroke-width="2.4"/></svg>
        @RosalindThorpeGardens
      </li>
      <li>
        <svg viewBox="0 0 24 24" aria-hidden="true"><circle cx="12" cy="12" r="10" fill="none" stroke="#0a272c" stroke-width="2"/><path d="M2 12h20M12 2c3 3 3 17 0 20M12 2c-3 3-3 17 0 20" fill="none" stroke="#0a272c" stroke-width="1.6"/></svg>
        www.RosalindThorpeGardens.example
      </li>
    </ul>
  </section>

  <section class="card card--back">
    <div class="brand-badge">Rosalind<br>Thorpe<br>Gardens</div>
  </section>
</body>
</html>
```